Moravel Aesthetic Doctor

I require an elegant, luxurious looking business card for my aesthetic business. I am a doctor and that will set me aside from competitors. I am planning to provide home and spa based treatments to clients with high expectations. I have attached my logo.

```html
<!DOCTYPE html>
<html lang="en">
<head>
<meta charset="utf-8">
<title>Moravel Aesthetic Doctor – Business Card</title>
<link href="https://fonts.googleapis.com/css2?family=Roboto:wght@300;400&family=Raleway:wght@500&display=swap" rel="stylesheet">
<style>
  :root {
    --bg: #c8c8c8;
    --card: #f3f3f3;
    --card-edge: #e4e4e4;
    --ink: #2f3236;
    --sky: #4aa3d8;
    --sky-light: #5cb1e0;
    --navy: #1f6fb2;
    --rule: #8c939c;
  }
  * { margin: 0; padding: 0; box-sizing: border-box; }
  html, body { width: 1200px; height: 576px; overflow: hidden; background: var(--bg); }
  .stage { position: relative; width: 1200px; height: 576px; }

  .card {
    position: absolute;
    border-radius: 10px;
    overflow: hidden;
    background: linear-gradient(180deg, #f8f8f8 0%, var(--card) 60%, var(--card-edge) 100%);
  }
  .card--front { left: 81px; top: 138px; width: 485px; height: 294px; }
  .card--back  { left: 602px; top: 138px; width: 481px; height: 292px; }

  .brand-name {
    position: absolute;
    font-family: "Roboto", sans-serif;
    font-weight: 300;
    color: var(--navy);
    line-height: 1.1;
    white-space: nowrap;
  }
  .card--front .brand-name { left: 0; right: 0; top: 82px; text-align: center; font-size: 32px; }
  .card--back .brand-name { left: 68px; top: 88px; font-size: 30px; }

  .services {
    position: absolute; left: 0; right: 0; top: 196px;
    text-align: center;
    font-family: "Roboto", sans-serif; font-size: 13px; line-height: 19px;
    color: var(--ink);
  }
  .services__sep { color: var(--sky); margin: 0 6px; }

  .offer-band {
    position: absolute; left: 0; right: 0; top: 240px; height: 34px;
    background: linear-gradient(90deg, var(--navy) 0%, #2a82c4 50%, var(--navy) 100%);
    color: #ffffff;
    font-family: "Raleway", sans-serif; font-weight: 500; font-size: 12.5px;
    letter-spacing: 1.3px;
    display: flex; align-items: center; justify-content: center;
  }

  .side-stripe { position: absolute; left: 0; top: 0; bottom: 0; width: 40px; background: var(--sky-light); }
  .side-rule { position: absolute; left: 44px; top: 0; bottom: 0; width: 3px; background: var(--rule); opacity: .7; }

  .person { position: absolute; left: 68px; top: 198px; font-family: "Roboto", sans-serif; }
  .person__name { font-size: 19px; font-weight: 300; color: var(--ink); }
  .person__creds { font-size: 10px; color: var(--sky); margin-left: 4px; }
  .person__title { font-size: 12.5px; color: var(--sky); margin-top: 4px; }

  .name-rule { position: absolute; left: 266px; top: 210px; width: 145px; height: 1px; background: var(--rule); }
  .social-pill {
    position: absolute; left: 406px; top: 200px; width: 75px; height: 20px;
    background: var(--sky-light);
    border-radius: 10px 0 0 10px;
    display: flex; align-items: center; gap: 5px; padding-left: 9px;
  }
  .social-pill__dot { width: 10px; height: 10px; border-radius: 50%; background: #ffffff; }

  .contacts {
    position: absolute; left: 68px; top: 252px;
    display: flex; gap: 10px; align-items: center;
    font-family: "Roboto", sans-serif; font-size: 12.5px; color: var(--ink);
    white-space: nowrap;
  }
  .contact { display: flex; align-items: center; gap: 5px; }
  .contact__icon { width: 17px; height: 17px; flex: none; }
  .contact__accent { color: var(--sky); }
</style>
</head>
<body>
<main class="stage">

  <section class="card card--front" aria-label="Business card front">
    <p class="brand-name">Moravel Aesthetic Doctor</p>
    <p class="services">
      Dermal Injectables<span class="services__sep">|</span>Plasma Facials<span class="services__sep">|</span>Microneedling<br>
      Skin Boosters<span class="services__sep">|</span>Excessive Sweating
    </p>
    <div class="offer-band">HOME AND SPA BASED TREATMENTS</div>
  </section>

  <section class="card card--back" aria-label="Business card back">
    <div class="side-stripe"></div>
    <div class="side-rule"></div>

    <p class="brand-name">Moravel Aesthetic Doctor</p>

    <div class="person">
      <p class="person__name">Dr Elise Varden<span class="person__creds">MRCPCH MD</span></p>
      <p class="person__title">Australasian Diploma of Aesthetic Medicine</p>
    </div>
    <div class="name-rule"></div>
    <div class="social-pill" aria-label="Social media">
      <span class="social-pill__dot"></span>
      <span class="social-pill__dot"></span>
    </div>

    <div class="contacts">
      <span class="contact">
        <svg class="contact__icon" viewBox="0 0 20 20" aria-hidden="true">
          <circle cx="10" cy="10" r="9" fill="none" stroke="#c9cdd2" stroke-width="1.2"/>
          <path d="M7 5.5l1.6 2.4-1 1.1c.6 1.3 1.5 2.2 2.6 2.8l1.1-1 2.3 1.6-.9 1.6c-3.4-.3-6.3-3.2-6.6-6.7z" fill="#4aa3d8"/>
        </svg>
        <span>0800 555 014</span>
      </span>
      <span class="contact">
        <svg class="contact__icon" viewBox="0 0 20 20" aria-hidden="true">
          <circle cx="10" cy="10" r="9" fill="none" stroke="#c9cdd2" stroke-width="1.2"/>
          <rect x="5" y="6.5" width="10" height="7" rx="1" fill="#4aa3d8"/>
          <path d="M5.3 7l4.7 3.6L14.7 7" fill="none" stroke="#ffffff" stroke-width="1"/>
        </svg>
        <span>elise@moravel.co.nz</span>
      </span>
      <span class="contact">
        <svg class="contact__icon" viewBox="0 0 20 20" aria-hidden="true">
          <circle cx="10" cy="10" r="9" fill="none" stroke="#c9cdd2" stroke-width="1.2"/>
          <circle cx="10" cy="10" r="5" fill="none" stroke="#4aa3d8" stroke-width="1.1"/>
          <ellipse cx="10" cy="10" rx="2.2" ry="5" fill="none" stroke="#4aa3d8" stroke-width="1"/>
          <path d="M5 10h10" stroke="#4aa3d8" stroke-width="1"/>
        </svg>
        <span>www.<span class="contact__accent">moravel</span>.co.nz</span>
      </span>
    </div>
  </section>

</main>
</body>
</html>
```